Tall Fern Roofing Business Card

Need a business card with the logo that was designed here

Contact Information for Business Card

Name, Title, Phone, Email, Website, Company name

```html
<!DOCTYPE html>
<html lang="en">
<head>
<meta charset="UTF-8">
<title>Tall Fern Roofing Business Card</title>
<link rel="stylesheet" href="https://fonts.googleapis.com/css2?family=Montserrat:wght@400;500;700&display=swap">
<style>
  :root {
    --page-bg: #e4e4e4;
    --card-white: #f7f7f7;
    --brand-blue: #2277bc;
    --brand-grey: #8a8d91;
    --ink: #3a3a3a;
    --on-blue: #ffffff;
  }
  * { box-sizing: border-box; margin: 0; padding: 0; }
  html, body {
    width: 1200px;
    height: 930px;
    overflow: hidden;
    background: var(--page-bg);
    font-family: "Montserrat", sans-serif;
  }
  .sheet {
    width: 1200px;
    height: 930px;
    display: flex;
    align-items: center;
    justify-content: center;
    gap: 40px;
  }
  .card {
    width: 540px;
    height: 309px;
    border-radius: 3px;
    box-shadow: 0 2px 6px rgba(0,0,0,0.12);
    position: relative;
  }
  .card-front {
    background: var(--card-white);
    padding: 70px 0 0 120px;
  }
  .card-back {
    background: var(--brand-blue);
    display: flex;
    align-items: center;
    justify-content: center;
  }
  .wordmark {
    font-weight: 700;
    font-size: 30px;
    letter-spacing: 0.5px;
    display: flex;
    align-items: center;
    gap: 10px;
  }
  .wordmark-mark {
    width: 14px;
    height: 14px;
  }
  .card-front .wordmark { color: var(--brand-blue); }
  .card-front .wordmark-mark { background: var(--brand-blue); }
  .card-back .wordmark { color: var(--on-blue); font-size: 34px; }
  .card-back .wordmark-mark { background: var(--on-blue); width: 16px; height: 16px; }
  .contact {
    margin-top: 30px;
    line-height: 1.35;
    color: var(--ink);
    font-size: 14px;
  }
  .contact-name {
    font-weight: 700;
    font-size: 16px;
    text-transform: uppercase;
    letter-spacing: 0.5px;
    color: var(--brand-blue);
  }
  .contact-name .surname { color: var(--brand-grey); }
  .contact-title {
    color: var(--brand-grey);
    font-weight: 500;
    margin-bottom: 6px;
  }
</style>
</head>
<body>
  <main class="sheet">
    <section class="card card-front">
      <div class="wordmark"><span class="wordmark-mark"></span>Tall Fern Roofing</div>
      <div class="contact">
        <p class="contact-name">Marcus <span class="surname">Hale</span></p>
        <p class="contact-title">Managing Director</p>
        <p>044-555 210 734</p>
        <p>info@tallfernroof.com</p>
        <p>www.tallfernroof.com</p>
      </div>
    </section>
    <section class="card card-back">
      <div class="wordmark"><span class="wordmark-mark"></span>Tall Fern Roofing</div>
    </section>
  </main>
</body>
</html>
```